UK landscaping company needs website

We, Brackwell Landscapes need a website design for a company based in Surrey, UK. The design should be bold and playful. We have three main areas of work driveways, paving and fencing. It shouldn't be too heavy in text and concentrate on the pictures from previous jobs we've completed. You may use stock images for the design, these can be changed if you are successful. Please don’t just copy the flyer it is just there to provide content.
We have a logo design which we would also like editing slightly.
Here are some of my local competitors
https://www.pelmarlandscapes.example.co.uk/

https://www.twinfirgardendesign.example.com/

https://kestbyrnlandscapes.example.co.uk/

Industry/Entity Type

Landscaping

Coding

Coded - Design and coding required

Number of Pages Required

3 page

Font styles to use
Sans Serif

Requirements
Must have
• Pictures of my previous jobs.
Must be mobile friendly
Easy to navigate
Nice to have
• Try to use different colours. It would be good to have some designs that aren’t just black and green.
I’d like some curves in the design.
Should not have
• We install hard landscaping. Think more building/construction and less plants and cutting grass.

```html
<!DOCTYPE html>
<html lang="en">
<head>
<meta charset="utf-8">
<title>Brackwell Landscapes</title>
<link rel="stylesheet" href="https://fonts.googleapis.com/css2?family=Poppins:wght@400;500;600&family=Lato:wght@400&display=swap">
<style>
:root{
  --green:#5ab330;
  --ink:#1e1e1e;
  --text:#333333;
  --white:#ffffff;
  --dark-bg:#2a2a2a;
  --dark-bg2:#333333;
  --footer:#dedede;
}
*{margin:0;padding:0;box-sizing:border-box}
html,body{width:1200px;height:3168px;overflow:hidden;background:var(--white)}
body{position:relative;font-family:'Poppins',sans-serif;color:var(--text)}
.btn{position:absolute;display:flex;align-items:center;justify-content:center;background:var(--green);color:var(--ink);font-family:'Poppins',sans-serif;font-size:15px;font-weight:500;text-transform:uppercase;height:43px}
.btn-outline{background:transparent;border:1px solid var(--green);color:var(--green)}

/* hero */
.hero{position:absolute;left:0;top:0;width:1200px;height:700px;overflow:hidden}
.hero-photo{position:absolute;inset:0;background:
  linear-gradient(180deg,#241e19 0%,#2e261f 26%,rgba(46,38,31,0) 34%),
  linear-gradient(158deg,#3f7a25 0%,#4f8f2c 36%,#9a6436 39%,#7b4f2c 50%,#a8a6a1 53%,#8e8c88 72%,#3b322b 76%,#2a241f 100%)}
.hero-shade{position:absolute;inset:0;background:linear-gradient(180deg,rgba(0,0,0,.45) 0%,rgba(0,0,0,.1) 30%,rgba(0,0,0,0) 55%)}
.brand{position:absolute;left:144px;top:20px;display:flex;align-items:center;gap:10px;color:var(--white);font-size:27px;font-weight:600;letter-spacing:.5px}
.brand-dot{width:14px;height:14px;border-radius:50%;background:var(--green)}
.phone{position:absolute;right:144px;top:10px;color:var(--white);font-size:23px;font-weight:600;display:flex;align-items:center;gap:10px}
.nav{position:absolute;right:144px;top:52px;display:flex;gap:39px;font-size:16px;color:var(--white)}
.nav .active{color:var(--green)}
.hero-title{position:absolute;right:144px;top:214px;text-align:right;color:var(--white);font-size:33px;font-weight:600;line-height:40px;text-transform:uppercase}
.arrow{position:absolute;top:325px}
.hero-curve{position:absolute;left:0;top:590px}

/* welcome */
.welcome-title{position:absolute;left:144px;top:790px;color:var(--green);font-size:31px;font-weight:600;line-height:40px;text-transform:uppercase}
.welcome-text{position:absolute;left:144px;top:884px;width:425px;font-family:'Lato',sans-serif;font-size:17px;line-height:30.5px;color:var(--text)}
.welcome-photo{position:absolute;left:623px;top:766px;width:433px;height:432px;background:
  linear-gradient(180deg,#1f2a17 0%,#34472a 18%,#4c5a38 26%,#cfd0cc 29%,#bfc1bf 40%,#7e8894 44%,#56606d 60%,#49525e 80%,#5a636f 100%);
  clip-path:path('M0 32 Q216 -14 433 14 L433 432 L0 432 Z')}

/* services */
.services{position:absolute;left:0;top:1280px;width:1200px;height:570px;background:linear-gradient(160deg,var(--dark-bg2),var(--dark-bg) 60%,#232323)}
.section-title{position:absolute;left:0;width:1200px;text-align:center;color:var(--green);font-size:32px;font-weight:600;text-transform:uppercase}
.service{position:absolute;top:1420px;width:270px;text-align:center;color:var(--white)}
.service h3{margin-top:26px;font-size:25px;font-weight:500}
.service p{margin-top:12px;font-family:'Lato',sans-serif;font-size:11px;line-height:21px}
.service .btn{position:relative;margin:16px auto 0;width:112px;font-size:14px}
.services-curve{position:absolute;left:0;top:1740px}

/* gallery */
.gallery-grid{position:absolute;left:144px;top:1971px;display:grid;grid-template-columns:repeat(3,297px);grid-auto-rows:191px;gap:9px 10px}

/* contact */
.contact{position:absolute;left:0;top:2508px;width:1200px;height:580px;background:linear-gradient(170deg,#2e2e2e,#262626 55%,#303030)}
.field{position:absolute;background:var(--white);font-size:13px;color:#444;padding:12px 15px}
.field-select::after{content:"";position:absolute;right:12px;top:18px;border:6px solid transparent;border-top:7px solid #555}
.footer-curve{position:absolute;left:0;top:2975px}
.footer{position:absolute;left:0;top:3060px;width:1200px;height:108px;background:var(--footer)}
.footer-links{position:absolute;left:144px;top:3080px;font-size:11px;color:var(--ink);word-spacing:2px}
.copyright{position:absolute;left:144px;top:3112px;font-size:11px;color:var(--ink)}
.social{position:absolute;top:3097px;width:18px;height:18px;border:2px solid #2b2b2b;border-radius:3px}
</style>
</head>
<body>

<header class="hero">
  <div class="hero-photo" role="img" aria-label="Garden with artificial lawn, timber sleeper steps, paved patio and rattan furniture"></div>
  <div class="hero-shade"></div>
  <div class="brand"><span>BRACKWELL LANDSCAPES</span><span class="brand-dot"></span></div>
  <div class="phone">
    <svg width="20" height="20" viewBox="0 0 24 24" aria-hidden="true"><path fill="#fff" d="M6.6 10.8a15.1 15.1 0 0 0 6.6 6.6l2.2-2.2c.3-.3.7-.4 1-.2 1.1.4 2.3.6 3.6.6.6 0 1 .4 1 1V20c0 .6-.4 1-1 1A17 17 0 0 1 3 4c0-.6.4-1 1-1h3.5c.6 0 1 .4 1 1 0 1.3.2 2.5.6 3.6.1.3 0 .7-.2 1z"/></svg>
    <span>555 014 2290</span>
  </div>
  <nav class="nav"><span class="active">Home</span><span>About Us</span><span>Services</span><span>Gallery</span><span>Contact Us</span></nav>
  <h1 class="hero-title">Vestibulum condimentum<br>risus posuere cursus</h1>
  <div class="btn" style="right:144px;top:304px;width:111px">Read more</div>
  <svg class="arrow" style="left:55px" width="22" height="34" viewBox="0 0 22 34" aria-hidden="true"><path d="M17 3 L5 17 L17 31" stroke="#fff" stroke-width="4" fill="none"/></svg>
  <svg class="arrow" style="left:1115px" width="22" height="34" viewBox="0 0 22 34" aria-hidden="true"><path d="M5 3 L17 17 L5 31" stroke="#fff" stroke-width="4" fill="none"/></svg>
  <svg class="hero-curve" width="1200" height="110" viewBox="0 0 1200 110" aria-hidden="true">
    <path d="M0 100 Q500 -10 1200 23 L1200 110 L0 110 Z" fill="var(--green)"/>
    <path d="M0 104 Q500 4 1200 32 L1200 110 L0 110 Z" fill="#fff"/>
  </svg>
</header>

<section class="welcome">
  <h2 class="welcome-title">Welcome to<br>Brackwell Landscapes</h2>
  <p class="welcome-text">Fusce sollicitudin lorem et luctus volutpat. Proin placerat dapibus gravida. In tristique tristique nulla eget hendrerit. Maecenas vel tortor accumsan quam varius imperdiet vel eget elit. Aenean facilisis tincidunt lectus, id dictum nisi luctus eget. Vivamus efficitur ex condimentum, malesuada eros eget, feugiat nibh. Sed tellus ex, imperdiet eget gravida sit amet, volutpat.</p>
  <div class="btn" style="left:144px;top:1124px;width:112px">Read more</div>
  <div class="welcome-photo" role="img" aria-label="Grey slab patio with rendered raised beds and potted flowers"></div>
</section>

<section class="services" role="img" aria-label="Dark backdrop of a pergola and trellis fencing"></section>
<h2 class="section-title" style="top:1350px">Our services</h2>

<div class="service" style="left:140px">
  <svg width="80" height="62" viewBox="0 0 80 62" aria-hidden="true" fill="none" stroke="#fff" stroke-width="3"><path d="M20 2 L2 60 H78 L60 2 Z"/><path d="M32 2 L24 60 M48 2 L56 60"/><rect x="36" y="10" width="8" height="10"/><rect x="35" y="27" width="10" height="12"/><rect x="34" y="46" width="12" height="12"/></svg>
  <h3>Driveways</h3>
  <p>Nulla tristique posuere molestie. Aliquam volutpat. Etiam quis aliquet risus. Duis ornare erat eget magna dapibus, in accumsan quam pharetra.</p>
  <div class="btn btn-outline">Read more</div>
</div>
<div class="service" style="left:465px">
  <svg width="62" height="62" viewBox="0 0 62 62" aria-hidden="true" fill="none" stroke="#fff" stroke-width="3"><rect x="2" y="2" width="58" height="58"/><rect x="8" y="8" width="46" height="46"/><path d="M8 24 H22 L28 8 M22 24 L26 38 H8 M26 38 L40 36 L46 54 M40 36 L54 30 M28 8 L40 20 L54 18 M40 20 L40 36"/></svg>
  <h3>Paving</h3>
  <p>Aliquam erat volutpat. Pellentesque blandit lacus eget nunc faucibus, et tincidunt eros viverra. Phasellus consequat sagittis nisi suscipit feugiat.</p>
  <div class="btn btn-outline">Read more</div>
</div>
<div class="service" style="left:789px">
  <svg width="74" height="62" viewBox="0 0 74 62" aria-hidden="true" fill="none" stroke="#fff" stroke-width="3"><path d="M4 60 V10 L9 3 L14 10 V60 M20 60 V10 L25 3 L30 10 V60 M36 60 V10 L41 3 L46 10 V60 M52 60 V10 L57 3 L62 10 V60 M68 60 V14"/><path d="M2 22 H72 M2 46 H72"/></svg>
  <h3>Fencing</h3>
  <p>Cras eget leo sed nunc hendrerit ultricies eu at nisl. Praesent iaculis faucibus urna sit amet lacinia. Maecenas consequat justo enim.</p>
  <div class="btn btn-outline">Read more</div>
</div>
<svg class="services-curve" width="1200" height="112" viewBox="0 0 1200 112" aria-hidden="true">
  <path d="M0 22 Q700 -14 1200 98 V112 H0 Z" fill="var(--green)"/>
  <path d="M0 28 Q700 -6 1200 104 V112 H0 Z" fill="#fff"/>
</svg>

<section class="gallery">
  <h2 class="section-title" style="top:1915px">Gallery</h2>
  <div class="gallery-grid">
    <div role="img" aria-label="Timber pergola over a grey patio" style="background:linear-gradient(180deg,#7d98c4 0%,#9aa9c0 14%,#b39a6e 18%,#a88f66 45%,#6b5a4c 55%,#c5c4bf 62%,#a9a8a3 100%)"></div>
    <div role="img" aria-label="New feather-edge fence beside a lawn" style="background:linear-gradient(180deg,#8aa35e 0%,#4f6a34 20%,#7e6648 24%,#8d7352 62%,#b8b4a8 66%,#5f9a2d 72%,#6fae33 100%)"></div>
    <div role="img" aria-label="Multi-tone block paved area" style="background:linear-gradient(180deg,#5a4c50 0%,#7a5a5a 35%,#8b5c55 65%,#6a4e52 100%)"></div>
    <div role="img" aria-label="Grey block paving with drainage channel" style="background:linear-gradient(180deg,#8a8676 0%,#5f7a3a 12%,#6b6c70 18%,#75767a 60%,#9a9b9c 100%)"></div>
    <div role="img" aria-label="Curved block paved driveway in front of a house" style="background:linear-gradient(180deg,#97a9c2 0%,#d6d5d2 22%,#c8c6c2 42%,#8e7c70 48%,#7e6c62 75%,#6b5b53 100%)"></div>
    <div role="img" aria-label="Long timber fence along a sunny lawn" style="background:linear-gradient(180deg,#4f7bc2 0%,#6d8fc4 18%,#5e7a3c 28%,#86815a 34%,#7b7652 68%,#6aa032 74%,#8ab83c 100%)"></div>
  </div>
  <div class="btn" style="left:544px;top:2385px;width:112px">View all</div>
</section>

<section class="contact" role="img" aria-label="Dark backdrop of stone steps"></section>
<h2 class="section-title" style="top:2580px">Contact us</h2>
<div class="field" style="left:144px;top:2637px;width:218px;height:40px">Name</div>
<div class="field" style="left:375px;top:2637px;width:218px;height:40px">Email</div>
<div class="field" style="left:607px;top:2637px;width:218px;height:40px">Phone</div>
<div class="field field-select" style="left:838px;top:2637px;width:218px;height:40px">Service for</div>
<div class="field" style="left:144px;top:2691px;width:912px;height:111px">Message</div>
<div class="btn" style="left:544px;top:2827px;width:112px">Submit</div>

<svg class="footer-curve" width="1200" height="90" viewBox="0 0 1200 90" aria-hidden="true">
  <path d="M0 95 Q600 -20 1200 12 V90 H0 Z" fill="var(--green)"/>
  <path d="M0 100 Q600 -12 1200 20 V90 H0 Z" fill="var(--footer)"/>
</svg>
<footer class="footer"></footer>
<div class="footer-links">Home &nbsp;| &nbsp;About Us &nbsp;| &nbsp;Services &nbsp;| &nbsp;Gallery &nbsp;| &nbsp;Contact Us</div>
<div class="copyright">Copyright &copy; 2020 &nbsp;Brackwell Landscapes. &nbsp;All rights reserved.</div>
<div class="social" style="left:944px" role="img" aria-label="Social link"></div>
<div class="social" style="left:988px" role="img" aria-label="Social link"></div>
<div class="social" style="left:1036px" role="img" aria-label="Social link"></div>

</body>
</html>
```